TRC Trifold

- Hello -
We are looking for an exciting trifold design for our residential roofing and interior remodeling company. Below is the website for more inspiration and images. We would like to include the Veteran Owned section somewhere on the back.

https://talvenbyroofingandconstruction.com/

Thank You,
Milo

```html
<!DOCTYPE html>
<html lang="en">
<head>
<meta charset="utf-8">
<title>TRC Trifold</title>
<link rel="stylesheet" href="https://fonts.googleapis.com/css2?family=Roboto:wght@400;500;700;900&display=swap">
<style>
:root{
  --maroon:#7a2327;
  --maroon-dark:#5e1a1d;
  --blush:#c9a5a7;
  --paper:#ffffff;
  --panel-grey:#ece8e6;
  --ink:#2f2f2f;
  --ink-soft:#444;
  --stage:#5d6166;
}
*{box-sizing:border-box;margin:0;padding:0}
html,body{width:1200px;height:2870px;overflow:hidden}
body{background:var(--stage);font-family:"Roboto",sans-serif;position:relative}
.trifold{position:absolute;left:30px;top:1030px;width:1140px;height:810px;display:flex;box-shadow:0 10px 30px rgba(0,0,0,.35)}
.panel{position:relative;width:380px;height:810px;overflow:hidden}

/* left panel */
.perks{background:var(--paper)}
.perks-header{height:158px;background:linear-gradient(135deg,var(--maroon) 0%,var(--maroon-dark) 100%);padding:28px 26px;border-bottom:7px solid var(--blush)}
.perks-title{color:#fff;font-weight:900;font-size:27px;line-height:33px;text-transform:uppercase}
.perks-list{list-style:none;padding:18px 26px 0 26px}
.perks-list li{display:flex;gap:12px;font-size:18.5px;line-height:23px;color:var(--ink);margin-bottom:21px}
.perks-list svg{flex:none;width:20px;height:20px;margin-top:2px}
.phone-bar{position:absolute;left:0;right:0;bottom:0;height:52px;background:var(--maroon);border-top:6px solid var(--blush);display:flex;align-items:center;padding-left:26px;gap:12px;color:#fff;font-weight:500;font-size:34px;letter-spacing:.5px}
.phone-bar svg{width:30px;height:30px}

/* middle panel */
.gallery{background:var(--maroon)}
.photo{position:absolute;border:3px solid #fff}
.photo-a{left:22px;top:28px;width:154px;height:114px;background:linear-gradient(180deg,#9fc0df 0%,#8a7c6c 60%,#4f6b3a 100%)}
.photo-b{left:190px;top:28px;width:154px;height:114px;background:linear-gradient(180deg,#a9cbe6 0%,#f1f1f1 55%,#556f3c 100%)}
.photo-c{left:22px;top:155px;width:322px;height:208px;background:linear-gradient(160deg,#f4f3f1 0%,#d9d6d2 55%,#6b5444 100%)}
.photo-d{left:22px;top:376px;width:154px;height:114px;background:linear-gradient(180deg,#bcd3e4 0%,#b9896a 55%,#5a8a3f 100%)}
.photo-e{left:190px;top:376px;width:154px;height:114px;background:linear-gradient(180deg,#f2f1ee 0%,#cfc8be 60%,#8a7a68 100%)}
.veteran{position:absolute;left:22px;right:22px;top:510px;bottom:0;background:var(--panel-grey);border-radius:55px 55px 0 0;text-align:center;padding-top:40px}
.veteran-title{color:var(--maroon);font-weight:700;font-size:31px;letter-spacing:.3px}

/* right panel */
.cover{background:var(--paper)}
.cover-photo{position:absolute;left:0;top:0;width:380px;height:262px;background:linear-gradient(180deg,#1d86e6 0%,#7fb6e8 45%,#d8c8b6 72%,#5b6b3c 100%)}
.brand{position:absolute;left:0;right:0;top:238px;height:78px;background:var(--paper);display:flex;align-items:center;justify-content:center;gap:12px}
.brand-square{width:34px;height:34px;background:var(--maroon)}
.brand-name{color:var(--maroon);font-weight:700;font-size:17px;letter-spacing:2px;line-height:21px;text-transform:uppercase}
.name-band{position:absolute;left:0;right:0;top:316px;height:56px;background:var(--maroon);color:#fff;font-weight:900;font-size:52px;line-height:56px;text-align:center;letter-spacing:1.5px}
.intro{position:absolute;left:0;right:0;top:372px;padding:6px 24px 0}
.intro-title{color:var(--maroon);font-weight:700;font-size:20.5px;letter-spacing:1px}
.intro-text{color:var(--ink-soft);font-size:12.5px;line-height:15px;margin-top:5px}
.service{position:absolute;left:6px;right:0;height:78px;background:var(--panel-grey);padding:8px 0 0 16px}
.service-exterior{top:474px}
.service-interior{top:562px}
.service-title{color:var(--maroon);font-weight:700;font-size:15px}
.service-items{display:flex;gap:28px;margin-top:8px;font-size:12px;line-height:16px;color:var(--ink)}
.service-tab{position:absolute;right:0;top:0;width:84px;height:78px;background:var(--maroon);clip-path:polygon(28% 0,100% 0,100% 100%,28% 100%,0 50%)}
.service-icon{position:absolute;right:14px;top:14px;width:50px;height:50px;border-radius:6px;background:rgba(255,255,255,.85)}
.floor{position:absolute;left:0;right:0;top:648px;height:110px;background:linear-gradient(180deg,#f6f6f6 0%,#d8d8d8 100%)}
</style>
</head>
<body>
<main class="trifold">

  <section class="panel perks">
    <header class="perks-header">
      <h2 class="perks-title">Perks that come from working with professionals</h2>
    </header>
    <ul class="perks-list">
      <li><svg viewBox="0 0 20 20"><path d="M2 11l5 5L18 3" fill="none" stroke="#7a2327" stroke-width="3"/></svg>Free Estimate</li>
      <li><svg viewBox="0 0 20 20"><path d="M2 11l5 5L18 3" fill="none" stroke="#7a2327" stroke-width="3"/></svg>Professional Interior</li>
      <li><svg viewBox="0 0 20 20"><path d="M2 11l5 5L18 3" fill="none" stroke="#7a2327" stroke-width="3"/></svg>Design Consultation</li>
      <li><svg viewBox="0 0 20 20"><path d="M2 11l5 5L18 3" fill="none" stroke="#7a2327" stroke-width="3"/></svg>Insurance Inspections assistance for an accurate assessment</li>
      <li><svg viewBox="0 0 20 20"><path d="M2 11l5 5L18 3" fill="none" stroke="#7a2327" stroke-width="3"/></svg>Insurance claim advocacy</li>
      <li><svg viewBox="0 0 20 20"><path d="M2 11l5 5L18 3" fill="none" stroke="#7a2327" stroke-width="3"/></svg>Once stop shop – General Contractor to assist with all of your Restoration and Renovation needs</li>
      <li><svg viewBox="0 0 20 20"><path d="M2 11l5 5L18 3" fill="none" stroke="#7a2327" stroke-width="3"/></svg>Referral Bonus</li>
      <li><svg viewBox="0 0 20 20"><path d="M2 11l5 5L18 3" fill="none" stroke="#7a2327" stroke-width="3"/></svg>Military Discount</li>
      <li><svg viewBox="0 0 20 20"><path d="M2 11l5 5L18 3" fill="none" stroke="#7a2327" stroke-width="3"/></svg>Free Architectural Consultation</li>
    </ul>
    <div class="phone-bar">
      <svg viewBox="0 0 24 24"><path d="M6.6 10.8a15 15 0 006.6 6.6l2.2-2.2a1 1 0 011-.25 11.4 11.4 0 003.6.57 1 1 0 011 1V20a1 1 0 01-1 1A17 17 0 013 4a1 1 0 011-1h3.5a1 1 0 011 1 11.4 11.4 0 00.57 3.6 1 1 0 01-.25 1z" fill="#fff"/></svg>
      630-555-0187
    </div>
  </section>

  <section class="panel gallery">
    <div class="photo photo-a" role="img" aria-label="Stone house exterior with roof"></div>
    <div class="photo photo-b" role="img" aria-label="White modern farmhouse with dark roof"></div>
    <div class="photo photo-c" role="img" aria-label="Remodeled bathroom with glass shower and freestanding tub"></div>
    <div class="photo photo-d" role="img" aria-label="Single-storey house with lawn"></div>
    <div class="photo photo-e" role="img" aria-label="Renovated open kitchen and dining room"></div>
    <div class="veteran">
      <h2 class="veteran-title">VETERAN OWNED</h2>
    </div>
  </section>

  <section class="panel cover">
    <div class="cover-photo" role="img" aria-label="Large stone house at dusk under blue sky"></div>
    <div class="brand">
      <span class="brand-square"></span>
      <span class="brand-name">Talvenby<br>Roofing &amp; Construction</span>
    </div>
    <h1 class="name-band">TALVENBY</h1>
    <div class="intro">
      <h2 class="intro-title">ROOFING AND CONSTRUCTION</h2>
      <p class="intro-text">Licensed and accredited company with over 20 years construction experience in Residential and Commercial Renovation and Restoration.</p>
    </div>
    <div class="service service-exterior">
      <h3 class="service-title">EXTERIOR HOME REMODELING</h3>
      <div class="service-items"><span>• Roofing<br>• Siding</span><span>• Gutters<br>• Soffit / Fascia</span></div>
      <div class="service-tab"><div class="service-icon" role="img" aria-label="House exterior icon"></div></div>
    </div>
    <div class="service service-interior">
      <h3 class="service-title">INTERIOR HOME REMODELING</h3>
      <div class="service-items"><span>• Home Improvement • Kitchen Remodeling<br>• Bathroom Remodeling</span></div>
      <div class="service-tab"><div class="service-icon" role="img" aria-label="Interior tools icon"></div></div>
    </div>
    <div class="floor" role="img" aria-label="Light weathered wood floor texture"></div>
    <div class="phone-bar">
      <svg viewBox="0 0 24 24"><path d="M6.6 10.8a15 15 0 006.6 6.6l2.2-2.2a1 1 0 011-.25 11.4 11.4 0 003.6.57 1 1 0 011 1V20a1 1 0 01-1 1A17 17 0 013 4a1 1 0 011-1h3.5a1 1 0 011 1 11.4 11.4 0 00.57 3.6 1 1 0 01-.25 1z" fill="#fff"/></svg>
      630-555-0187
    </div>
  </section>

</main>
</body>
</html>
```